Stationary Set Rebrand for Brennick

We are a Canadian Distribution and Service Company that was established in 1969. Over the past 5 decades we have expanded our business and have warehouses across Canada. We specialize in adhesive tapes, adhesives, films, safety, warehouse, shipping, janitorial and packaging supplies.

We have updated our logo design and would like a new corporate branding identity that includes a new fresh Stationary Set (Business Cards, Letterhead, Letterhead MS Word, Envelope, Presentation Folders, Email Signatures, Notepad Covers, etc.)

Target Market(s)

Industrial Business Sector

Font styles to use
Sans Serif

Colors
0054AA
0677BA
7BADD7
CADEEF
E8F1F8
0094D4
00A9DD
6FCCEA
C7EBF8
E9F6FB
00AB8E
00BBA5
67D7C9
C6EFE9
E9F9F6
EB3D1F
EC4F4E
F09395
F8D3D4
FCEDEE

Requirements
Should not have
• Colors not too light, darker colours preferred

```html
<!DOCTYPE html>
<html lang="en">
<head>
<meta charset="utf-8">
<title>Brennick business card</title>
<link href="https://fonts.googleapis.com/css2?family=Open+Sans:wght@400;700&display=swap" rel="stylesheet">
<style>
  :root {
    --stage: #2b2b2b;
    --paper: #ffffff;
    --ink: #1c1c1c;
    --ink-soft: #555555;
    --accent: #d81e24;
    --card-dark: #1f1f1f;
    --pattern-a: #262626;
    --pattern-b: #3a3a3a;
  }
  html, body {
    margin: 0;
    width: 1200px;
    height: 900px;
    overflow: hidden;
    background: var(--stage);
    font-family: "Open Sans", Arial, sans-serif;
  }
  .card {
    position: absolute;
    left: 250px;
    width: 700px;
    height: 400px;
    box-shadow: 0 10px 30px rgba(0,0,0,0.5);
    overflow: hidden;
  }
  .card--front { top: 35px; background: var(--paper); }
  .card--back { top: 465px; background: var(--card-dark); }

  .holder { position: absolute; left: 44px; top: 44px; }
  .holder__name {
    margin: 0;
    color: var(--accent);
    font-weight: 700;
    font-size: 28px;
    letter-spacing: 0.5px;
  }
  .holder__role {
    margin: 2px 0 0;
    color: var(--ink-soft);
    font-size: 20px;
  }
  .divider {
    position: absolute;
    left: 44px;
    top: 128px;
    width: 590px;
    height: 1px;
    background: var(--ink-soft);
  }
  .contacts {
    position: absolute;
    left: 44px;
    top: 142px;
    margin: 0;
    padding: 0;
    list-style: none;
    color: var(--ink-soft);
    font-size: 19px;
    line-height: 30px;
  }
  .contacts li { display: flex; align-items: center; gap: 8px; }
  .contacts svg { width: 16px; height: 16px; fill: var(--accent); }

  .wordmark {
    position: absolute;
    right: 60px;
    top: 40px;
    display: flex;
    align-items: center;
    gap: 10px;
    color: var(--ink);
    font-weight: 700;
    font-size: 64px;
    line-height: 1;
  }
  .wordmark__dot {
    width: 14px; height: 14px; border-radius: 50%;
    background: var(--accent);
  }
  .address {
    position: absolute;
    right: 66px;
    top: 146px;
    margin: 0;
    text-align: right;
    color: var(--ink-soft);
    font-size: 19px;
    line-height: 28px;
    font-style: normal;
  }
  .wave { position: absolute; left: 0; bottom: 0; width: 700px; height: 170px; }

  .pattern-field {
    position: absolute; inset: 0;
    background: linear-gradient(135deg, var(--pattern-a), var(--pattern-b) 50%, var(--pattern-a));
  }
  .card--back .wordmark { color: var(--paper); top: 160px; }
</style>
</head>
<body>
  <section class="card card--front" aria-label="Business card front">
    <div class="holder">
      <h1 class="holder__name">JONATHAN SMITH</h1>
      <p class="holder__role">Managing Director</p>
    </div>
    <div class="divider"></div>
    <ul class="contacts">
      <li><svg viewBox="0 0 16 16"><path d="M3 1h3l1 4-2 1a9 9 0 0 0 5 5l1-2 4 1v3c0 1-1 2-2 2A13 13 0 0 1 1 3c0-1 1-2 2-2z"/></svg>044-123 456 789</li>
      <li><svg viewBox="0 0 16 16"><path d="M1 3h14v10H1z M1 3l7 6 7-6" fill="none" stroke="#d81e24" stroke-width="1.8"/></svg>info@webname.com</li>
      <li><svg viewBox="0 0 16 16"><circle cx="8" cy="8" r="7"/></svg>www.websitename.com</li>
    </ul>
    <div class="wordmark"><span>Brennick</span><span class="wordmark__dot"></span></div>
    <address class="address">Your Address, City<br>State, Zip 0000</address>
    <svg class="wave" viewBox="0 0 700 170" preserveAspectRatio="none">
      <path d="M0 20 C150 120 400 140 700 120 L700 170 L0 170 Z" fill="#1f1f1f"/>
      <path d="M0 14 C160 110 420 128 700 112" fill="none" stroke="#d81e24" stroke-width="5"/>
      <path d="M0 8 C170 100 430 120 700 106" fill="none" stroke="#ffffff" stroke-width="3"/>
    </svg>
  </section>

  <section class="card card--back" aria-label="Business card back">
    <div class="pattern-field" role="img" aria-label="Repeating leaf pattern in dark greys"></div>
    <div class="wordmark"><span>Brennick</span><span class="wordmark__dot"></span></div>
  </section>
</body>
</html>
```